Need Website Design for Non-Profit Veteran Site

I am looking for a very talented creative website designer for a modern feel. I'll give a little bit of guidance around what I am looking for and then your creative juices should kick in and design away. I have already purchased the domain but will need hosting (at least temporarily) and the creative design work done.The website domain is militarydocs.orgI am looking to attract current and veteran military providers (doctors, nurse practitioners, physician assistants, etc) to join and signup for membership. They would pay a yearly fee to join. Would need membership categories $135 for Provider, $55 Student, $100 for Retired, and Organization (Organization would be broken down into Less than 100 ($200), 100-249 ($250), 250-499 ($300), 500-999 ($400), 1,000-2,999 ($500), and 3,000 ($700). Would need Benefit built out and would need to accept money through CoinVane and other means. Since it's a new organization just starting, would also need a Donate button to get people to donate if they want any amount they would like. The second part of the website is that once they join, they will have acess to a list of all other providers who have registered within the website (not exportable) so they can connect with one another. If they want to see contact information this will be included in their fee as a benefit to socialize with one another. As part of the website, there will be another Veteran's portal so veterans who would like to connect with a provider around a particular speciality can reach out and request help from the doctor writing a nexus letter or letter to support the veteran who is filing a claim with the BQ. Veterans would pay a yearly sign-up fee of $30.00 and would need their membership benefits displayed. They would have access to a list of veterans in their region by state and distance, and can reach out to doctors to get their help. If a doctor and veteran agree, sharable inforamtion of medical hipaa documents can be exchanged via the website. The physician and veteran can negotiate a fee through the website only and share their details. This is a separate fee for this type of process between the provider and veteran. We will collect a $250 fee for admin on each of these and each project the veteran does with the provider will cost $450 (so essentially the doctor gets paid $450 and i get $250.00. This model could be changed over time as we start to test this out). A good example of 50% of what I'm looking for is something like the following website: https://www.lpkt.org/ It has some of the features but not all and my site should be more modernized to attract the veteran and military providers.

Target Market(s)

Current and retired military providers and veterans

Industry/Entity Type

Non Profit

Number of Pages Required

1 page

Requirements
Must have
• Military Design
• Modern Feel (Example templates for feel -https://quillmoth.com/free-photoshop-psd-web-design-template/)
• Donation box
• Stuff mentioned in the description)
Nice to have
• Open to feedback
Should not have
• Open to feedback

```html
<!DOCTYPE html>
<html lang="en">
<head>
<meta charset="utf-8">
<title>Harborwell Docs</title>
<link rel="stylesheet" href="https://fonts.googleapis.com/css2?family=Poppins:ital,wght@0,400;0,500;0,600;0,700;1,400&display=swap">
<style>
:root{
  --camo-dark:#2f3f1c;
  --camo-mid:#44582a;
  --olive:#566c25;
  --olive-light:#8a9e4a;
  --nav-sep:#6e8438;
  --sage:#c6ccb4;
  --paper:#f1f1ec;
  --ink:#2b2b2b;
  --line:#333333;
  --white:#ffffff;
}
*{box-sizing:border-box;margin:0;padding:0}
html,body{width:1101px;height:1200px;overflow:hidden}
body{
  position:relative;
  font-family:'Poppins',sans-serif;
  color:var(--ink);
  background:linear-gradient(180deg,var(--sage) 330px,#e4e6dc 700px,var(--paper) 977px);
}
.camo-top{position:absolute;left:0;top:0;width:1101px;height:330px;
  background:radial-gradient(ellipse at 20% 30%,var(--camo-mid),transparent 60%),radial-gradient(ellipse at 85% 70%,#3d5024,transparent 55%),var(--camo-dark)}
.topbar{position:absolute;left:215px;top:0;width:671px;height:32px;background:#dde1d1;
  display:flex;align-items:center;justify-content:space-between;padding:0 14px 0 17px;font-size:8px;white-space:nowrap}
.topbar nav a{margin-right:15px;color:var(--ink);text-decoration:none}
.call{font-weight:600;font-size:9.5px;display:flex;align-items:center;gap:6px}
.header{position:absolute;left:215px;top:32px;width:671px;height:70px;
  background:linear-gradient(180deg,#e3e6da,#f3f3ef)}
.brand{position:absolute;left:16px;top:21px;font-size:21px;font-weight:700;color:#2d2d2d;letter-spacing:-.3px;white-space:nowrap}
.search{position:absolute;left:375px;top:20px;width:216px;height:26px;border:1px solid #8b8f80;border-radius:14px;
  font-size:8px;font-style:italic;color:#444;padding:7px 15px;background:#f6f6f2}
.search svg{position:absolute;right:10px;top:8px}
.join{position:absolute;left:599px;top:20px;width:61px;height:26px;border-radius:14px;background:var(--olive);
  color:var(--white);font-size:8.5px;font-weight:500;display:flex;align-items:center;justify-content:center}
.mainnav{position:absolute;left:215px;top:102px;width:671px;height:40px;background:var(--olive);
  font-size:10px;color:var(--white);overflow:hidden}
.mainnav span{position:absolute;top:0;line-height:40px;white-space:nowrap}
.mainnav i{position:absolute;top:0;width:1px;height:40px;background:var(--nav-sep);transform:skewX(-25deg)}
.hero{position:absolute;left:215px;top:142px;width:671px;height:293px;
  background:linear-gradient(90deg,#6a6250 0%,#8a7c64 35%,#a8957a 60%,#b9aa93 100%);color:var(--white);text-align:center}
.hero h1{position:absolute;left:0;right:0;top:93px;font-size:36px;font-weight:500;line-height:44px}
.hero p{position:absolute;left:0;right:0;top:143px;font-size:14px;line-height:19px}
.dots{position:absolute;left:268px;top:265px;display:flex;gap:3px}
.dots i{display:block;width:32px;height:3px;background:var(--white)}
.dots i.off{background:transparent;border:1px solid var(--white)}
.card{position:absolute;top:458px;height:327px;background:var(--white);border:2px solid var(--line);overflow:hidden}
.c1{left:215px;width:189px}
.c2{left:416px;width:229px}
.c3{left:656px;width:229px}
.actions{height:139px;border-bottom:2px solid var(--line);background:linear-gradient(180deg,#fafafa,#eeeeea);padding:10px 10px 0 10px}
.action{height:36px;border:2px solid var(--line);border-radius:18px;margin-bottom:5px;display:flex;align-items:center;
  font-size:10px;font-weight:600;background:#f3f3f1;white-space:nowrap}
.action .ico{width:28px;height:28px;border-radius:50%;background:var(--olive);margin:0 8px 0 2px;display:flex;align-items:center;justify-content:center;flex:none}
h2{font-size:19px;font-weight:600;color:var(--olive);line-height:23px}
.news h2{margin:6px 0 6px 10px}
.news ul{list-style:none;padding-left:9px;font-size:8px}
.news li{height:20.8px;display:flex;align-items:center;white-space:nowrap}
.news li::before{content:"";width:5px;height:5px;border-radius:50%;background:var(--olive);margin-right:5px;flex:none}
.photo{margin:9px 8px 0 9px;height:126px}
.ph1{background:linear-gradient(135deg,#d9d3c8,#b5a58a 55%,#7d7a5e)}
.ph2{background:linear-gradient(135deg,#e8e0d4,#c9b9a3 50%,#7e7a60)}
.body{padding:0 9px}
.body h2{margin:13px 0 6px 1px}
.lead{font-size:12px;line-height:17px;margin-bottom:11px}
.text{font-size:8.2px;line-height:14.4px}
.btn{display:inline-flex;align-items:center;justify-content:center;width:74px;height:25px;border-radius:13px;
  background:var(--olive);color:var(--white);font-size:9px;margin-top:11px}
.quote{position:absolute;left:215px;top:810px;width:671px;height:148px;background:var(--olive-light);text-align:center;color:var(--white)}
.quote svg{position:absolute;left:318px;top:21px}
.quote p{position:absolute;left:0;right:0;top:60px;font-size:9.6px;font-style:italic;line-height:19.3px}
.quote cite{position:absolute;left:0;right:0;top:116px;font-style:normal;font-weight:600;font-size:10.5px}
.footer{position:absolute;left:0;top:977px;width:1101px;height:223px;color:var(--white);
  background:radial-gradient(ellipse at 30% 40%,#4a5f2c,transparent 60%),radial-gradient(ellipse at 80% 80%,#3e5226,transparent 55%),var(--camo-dark)}
.fcol{position:absolute;top:0;height:175px}
.fcol h3{position:absolute;top:29px;font-size:12.5px;font-weight:400;white-space:nowrap}
.fcol ul{position:absolute;top:56px;list-style:none;font-size:9px;line-height:19.6px;white-space:nowrap}
.divider{position:absolute;top:0;width:1px;height:175px;background:#8a937a}
.field{position:absolute;left:712px;width:174px;height:26px;background:var(--white);color:#333;font-size:8px;padding:8px 11px}
.signup{position:absolute;left:712px;top:119px;width:174px;height:26px;background:var(--olive-light);font-size:8.5px;font-weight:500;
  display:flex;align-items:center;justify-content:center}
.rule{position:absolute;left:215px;top:175px;width:671px;height:1px;background:#8a937a}
.social{position:absolute;left:216px;top:186px;display:flex;gap:3px}
.social i{display:block;width:23px;height:23px;border:1px solid var(--white);border-radius:50%}
.legal{position:absolute;right:215px;top:192px;font-size:9px;white-space:nowrap}
</style>
</head>
<body>
<div class="camo-top"></div>

<div class="topbar">
  <nav><a>About Us</a><a>Resources</a><a>Certification</a><a>International</a></nav>
  <div class="call"><svg width="8" height="8" viewBox="0 0 24 24"><path fill="#333" d="M6.6 10.8a15 15 0 0 0 6.6 6.6l2.2-2.2c.3-.3.7-.4 1-.2 1.1.4 2.3.6 3.6.6.6 0 1 .4 1 1V20c0 .6-.4 1-1 1A17 17 0 0 1 3 4c0-.6.4-1 1-1h3.5c.6 0 1 .4 1 1 0 1.3.2 2.5.6 3.6.1.3 0 .7-.2 1z"/></svg>Call Us: 1850 42 77 16</div>
</div>

<header class="header">
  <div class="brand">HARBORWELL DOCS</div>
  <div class="search">Search<svg width="8" height="8" viewBox="0 0 24 24"><circle cx="10" cy="10" r="6" fill="none" stroke="#333" stroke-width="3"/><path d="M15 15l6 6" stroke="#333" stroke-width="3"/></svg></div>
  <div class="join">JOIN</div>
</header>

<nav class="mainnav">
  <span style="left:20px">Home</span><i style="left:62px"></i>
  <span style="left:83px">Membership</span><i style="left:160px"></i>
  <span style="left:176px">Research</span><i style="left:237px"></i>
  <span style="left:254px">Conferences</span><i style="left:330px"></i>
  <span style="left:348px">Practices</span><i style="left:408px"></i>
  <span style="left:425px">Programs</span><i style="left:487px"></i>
  <span style="left:505px">Publications</span><i style="left:578px"></i>
  <span style="left:596px">Contact Us</span>
</nav>

<section class="hero" role="img" aria-label="Photo of a uniformed service member talking with a clinician holding a clipboard">
  <h1>Harborwell Docs</h1>
  <p>Sed ut perspiciatis unde omnis iste natus<br>sit voluptatSed ut perspiciatis unde.</p>
  <div class="dots"><i></i><i></i><i class="off"></i><i></i></div>
</section>

<article class="card c1">
  <div class="actions">
    <div class="action"><span class="ico"><svg width="14" height="14" viewBox="0 0 24 24"><circle cx="10" cy="7" r="4.5" fill="#fff"/><path d="M2 22c0-5 4-8 8-8s8 3 8 8z" fill="#fff"/><path d="M19 12v6M16 15h6" stroke="#fff" stroke-width="2"/></svg></span>Sign up for Membership</div>
    <div class="action"><span class="ico"><svg width="14" height="14" viewBox="0 0 24 24"><circle cx="12" cy="12" r="10" fill="none" stroke="#fff" stroke-width="2"/><text x="12" y="17" font-size="13" font-weight="700" fill="#fff" text-anchor="middle" font-family="Poppins,sans-serif">$</text></svg></span>Donate</div>
    <div class="action"><span class="ico"><svg width="14" height="14" viewBox="0 0 24 24"><path d="M6 5h12l-2 3H8z" fill="#fff"/><circle cx="12" cy="11" r="3.5" fill="#fff"/><path d="M4 22c0-5 4-7 8-7s8 2 8 7z" fill="#fff"/></svg></span>Veterans Sign up</div>
  </div>
  <div class="news">
    <h2>News</h2>
    <ul>
      <li>Sed ut erspiciatis unde omnis iste natu</li>
      <li>Eror sit voluptatem accusantium dolor</li>
      <li>Mqloruloe laudantium, totam rem ape</li>
      <li>Riam, eaque lorisa quae ab illo invent</li>
      <li>Ore veritaloe lorisa quae abtis.</li>
      <li>Riam, eaque lorisa quae ab illo invent</li>
      <li>Ore veritaloe lorisa quae abtis.</li>
    </ul>
  </div>
</article>

<article class="card c2">
  <div class="photo ph1" role="img" aria-label="Photo of a clinician shaking hands with a uniformed service member"></div>
  <div class="body">
    <h2>Welcome!</h2>
    <p class="lead">Lorem ipsum dolor sit ameconse ctetur ad ipsum dipis.</p>
    <p class="text">Sed ut perspiciatis unde omnis iste natus eror sit voluptatem accusantium dolore mqloruloe laudantium, totam rem aperiam, eaque lorisa quae ab illo inventore veritalotis.</p>
    <span class="btn">Read More</span>
  </div>
</article>

<article class="card c3">
  <div class="photo ph2" role="img" aria-label="Photo of a clinician taking notes while a service member listens"></div>
  <div class="body">
    <h2>What We Do</h2>
    <p class="lead">Lorem ipsum dolor sit ameconse ctetur ad ipsum dipis.</p>
    <p class="text">Sed ut perspiciatis unde omnis iste natus eror sit voluptatem accusantium dolore mqloruloe laudantium, totam rem aperiam, eaque lorisa quae ab illo inventore veritalotis.</p>
    <span class="btn">Read More</span>
  </div>
</article>

<section class="quote">
  <svg width="34" height="22" viewBox="0 0 34 22"><path d="M2 22V13C2 6 5 2 11 0l1 3c-3 1-5 4-5 7h5v12zM20 22V13c0-7 3-11 9-13l1 3c-3 1-5 4-5 7h5v12z" fill="#a9b97a"/></svg>
  <p>Lorem ipsum dolor sit amet, consectetur adipiscing elit, sed do eiusmod tempor incididunt ut<br>dolore magna aliqua. Ut enim ad minim veniam,Lorem ipsum dolor sit amet, consectetur adipiscing<br>elied do eiusmod tempor incididunt ut labore et dolore magna aliqua. Ut enim ad minim am,</p>
  <cite>Dara Quell, City Name</cite>
</section>

<footer class="footer">
  <div class="fcol" style="left:215px"><h3>Harborwell docs</h3>
    <ul><li>Sed utersipiciatiserspiciatis unde</li><li>ers piciatis undeed uerspiciatiem</li><li>omnis teatuerspiciaterspi unde</li><li>ed uerspiciaciatsit</li></ul></div>
  <div class="divider" style="left:385px"></div>
  <div class="fcol" style="left:415px"><h3>Links</h3>
    <ul><li>Membership</li><li>Research</li><li>Conferences</li><li>Legislation</li><li>Blog</li></ul></div>
  <div class="divider" style="left:494px"></div>
  <div class="fcol" style="left:537px"><h3>About</h3>
    <ul><li>Sed uterspicipiciatatis</li><li>Perspiciatispiciatis undun</li><li>Perspiciatis upiciande</li><li>Sed uerspicipiciatis unda</li><li>Comnisteapiciatitusit</li></ul></div>
  <div class="divider" style="left:677px"></div>
  <div class="fcol" style="left:711px"><h3>Sign up Newsletter</h3></div>
  <div class="field" style="top:60px">Name:</div>
  <div class="field" style="top:89px">Email:</div>
  <div class="signup">SIGN UP</div>
  <div class="rule"></div>
  <div class="social"><i></i><i></i><i></i><i></i></div>
  <div class="legal">© 2018 Harborwell Docs. Privacy Policy | Terms of Use</div>
</footer>
</body>
</html>
```